Website design needed for gift based dropship website

I am building a dropshipping website that will create gift based merchandise and send it out to our clients customers for them. Our clients will sell products and when a customer buys from them, we create the item and send it out to the customer.

I am looking for a very similar website to stitchora.com - that website is doing a very similar thing to what i am doing but where the stitchora website is based around clothing, my website will be based around gifts. Another website that i like that is doing a similar thing to what i will do is pelvane.com

I require 2 pages to be made:
1) The home page
2) A landing page for a free product giveaway offer

1) THE HOME PAGE
The home page should be a merger of the two previously stated websites (www.pelvane.com and www.stitchora.com). The style fo the homepage should be based on the logo that is attached and the colour scheme should be similar but basic.

2) THE LANDING PAGE
The landing page will be giving away a free mobile phone cover. The page needs to have some mobile phone covers for different phones all with random designs on. The page should state that they can have any design that they want and they do not pay for the phone (they only pay for shipping).

Menu pages and text should be taken from the stitchora.com website.

Target Market(s)

18 - 40 year old males. People who like the idea of earning extra money in their spare time but aren't too sure how to do it. Semi-professional jobs.

Font styles to use
Serif
Sans Serif
Decorative
Script

Colors

Designer to choose colors to be used in the design.

Requirements
Must have
• A "how it works" image where the dropshipping process is explained to a visitor to the website (similar to the one on the stitchora "how it works page")
Nice to have
• Testimonial area on homepage
Should not have
• Homepage should not have:
• - "latest orders from" area
• - Video
• - Warehousing/fulfilment area
• - Integration area

```html
<!DOCTYPE html>
<html lang="en">
<head>
<meta charset="utf-8">
<title>Brightmoor Gifts – Free Mobile Phone Cover</title>
<link rel="stylesheet" href="https://fonts.googleapis.com/css2?family=Roboto+Condensed:wght@400;700&family=Roboto:wght@400;500&family=Caveat:wght@400;600&display=swap">
<style>
:root{
  --red:#e8150c;
  --maroon:#3f0c1f;
  --ink:#2b2b2b;
  --muted:#8b8383;
  --grey:#e5e2e2;
  --light:#f2f1f1;
  --line:#cfc8c8;
  --white:#ffffff;
}
*{box-sizing:border-box;margin:0;padding:0}
html,body{width:1200px;height:3197px;overflow:hidden}
body{position:relative;background:var(--white);font-family:"Roboto",Arial,sans-serif;color:var(--ink)}
.abs{position:absolute}
.cond{font-family:"Roboto Condensed",Arial,sans-serif}
.script{font-family:"Caveat",cursive}

/* header */
.header{left:0;top:0;width:1200px;height:207px;background:linear-gradient(#fff 0 38px,#f6f6f6 38px,#fff 120px)}
.account{right:50px;top:7px;display:flex;gap:36px;font-size:17px;color:var(--ink)}
.brand{display:flex;align-items:center;gap:12px}
.brand-mark{width:26px;height:26px;background:var(--red)}
.brand-name{font-family:"Roboto",sans-serif;font-weight:500;font-size:26px;color:var(--ink);white-space:nowrap}
.nav{left:430px;top:54px;width:612px;display:flex;justify-content:space-between;font-size:17px;padding-bottom:20px;border-bottom:1px solid var(--line)}
.social{left:776px;top:134px;display:flex;align-items:center;gap:22px;font-size:24px;color:var(--red)}
.social .dot{width:20px;height:20px;border-radius:50%;background:var(--red)}

/* hero */
.hero{left:0;top:207px;width:1200px;height:658px;background:var(--grey)}
.hero-kicker{left:124px;top:278px;font-size:58px;color:var(--red)}
.hero-title{left:124px;top:355px;font-weight:700;font-size:88px;line-height:90px;color:var(--maroon)}
.hero-title em{font-style:normal;color:var(--red)}
.hero-sub{left:124px;top:542px;width:480px;font-size:26px;line-height:36px;color:#1a1a1a}
.pill{left:124px;top:643px;width:313px;height:36px;border:2px solid #333;border-radius:18px;font-size:20px;text-align:center;line-height:32px;letter-spacing:.5px}
.btn{background:var(--red);color:#fff;font-family:"Roboto Condensed",sans-serif;font-weight:700;text-align:center}
.hero-btn{left:126px;top:710px;width:394px;height:62px;font-size:28px;line-height:62px}
.hero-phones{left:690px;top:256px;width:320px;height:564px;border-radius:30px;background:linear-gradient(160deg,#f7d43c 0 35%,#eeeeee 55%,#a03bb4 100%)}
.badge{border-radius:50%;display:flex;flex-direction:column;align-items:center;justify-content:center;color:#fff;text-align:center}
.badge .small{font-size:15px}
.badge .price{font-family:"Roboto Condensed",sans-serif;font-weight:700;text-decoration:line-through}
.hero-badge{left:631px;top:309px;width:128px;height:128px;background:var(--red)}
.hero-badge .price{font-size:36px}

.limited{left:0;top:883px;width:1200px;text-align:center;font-weight:700;font-size:52px;color:var(--red);letter-spacing:1px}

/* info */
.info{left:0;top:972px;width:1200px;height:400px;background:linear-gradient(#efeeee,#fff)}
.info-title{left:157px;top:1046px;font-weight:700;font-size:58px;color:var(--maroon)}
.copy{font-size:22px;line-height:39px;letter-spacing:.6px;color:#333}
.info-copy{left:157px;top:1128px;width:640px}
.info-phone{left:870px;top:1029px;width:160px;height:335px;border-radius:22px;background:linear-gradient(#fff,#f4e6e6);border:3px solid #ddd}

/* faq */
.rule{height:2px;background:#8d7a80}
.faq-icon{left:545px;top:1411px;width:128px;height:128px;border-radius:50%;background:var(--maroon)}
.faq-title{left:0;top:1565px;width:1200px;text-align:center;font-weight:700;font-size:62px;color:#4c393f}
.faq-col{width:420px}
.faq-q{font-family:"Roboto Condensed",sans-serif;font-weight:700;font-size:22px;color:#111;margin-bottom:4px}
.faq-a{font-size:14px;line-height:17px;color:var(--muted);margin-bottom:40px}
.faq-divider{left:597px;top:1705px;width:1px;height:238px;background:#ddd}

/* offer band */
.band{left:0;top:2065px;width:1200px;height:151px;background:var(--red)}
.band-title{left:148px;top:2104px;font-weight:700;font-size:58px;color:#fff;white-space:nowrap}
.band-title em{font-style:normal;color:var(--maroon)}
.band-badge{left:843px;top:2024px;width:214px;height:214px;background:var(--maroon)}
.band-badge .small{font-size:23px}
.band-badge .price{font-size:62px}

.offer-phones{left:170px;top:2306px;width:182px;height:251px;border-radius:18px;background:linear-gradient(160deg,#f7d43c 0 30%,#eeeeee 55%,#a03bb4 100%)}
.offer-copy{left:416px;top:2313px;width:640px}
.offer-note{left:0;top:2627px;width:1200px;text-align:center;font-size:36px;color:#222}
.cta-box{left:147px;top:2698px;width:895px;height:140px;border:2px solid #d6d6d6}
.cta-btn{left:258px;top:2734px;width:663px;height:68px;font-size:34px;line-height:68px}

/* footer */
.footer{left:0;top:2915px;width:1200px;height:245px;background:var(--light)}
.footer-brand{left:149px;top:2975px}
.footer-brand .brand-mark{width:22px;height:22px}
.footer-brand .brand-name{font-size:22px}
.footer-phone{left:149px;top:3091px;font-family:"Roboto Condensed",sans-serif;font-weight:700;font-size:26px;color:var(--maroon);display:flex;align-items:center;gap:10px}
.footer-col{top:2960px;font-size:12px;line-height:28px;color:#555}
.footer-col h4{font-family:"Roboto Condensed",sans-serif;font-weight:700;font-size:17px;color:#222;margin-bottom:8px;letter-spacing:.5px}
.bottom-bar{left:0;top:3160px;width:1200px;height:37px;background:var(--red);color:#fff;font-size:12px}
.bottom-bar span{position:absolute;top:12px}
</style>
</head>
<body>

<!-- header -->
<div class="abs header"></div>
<div class="abs account"><span>&#9679; Login</span><span>&#9679; Sign up</span></div>
<div class="abs brand" style="left:149px;top:104px">
  <div class="brand-mark"></div>
  <div class="brand-name">Brightmoor Gifts</div>
</div>
<nav class="abs nav"><span>Products</span><span>How it works</span><span>Mockup Generator</span><span>Shipping</span><span>FAQ</span><span>Blog</span></nav>
<div class="abs social"><span class="script">Social Media &rarr;</span><span class="dot"></span><span class="dot"></span><span class="dot"></span></div>

<!-- hero -->
<section class="abs hero"></section>
<div class="abs hero-kicker script">get your &rarr;</div>
<h1 class="abs hero-title cond"><em>Free</em> Mobile<br>Phone Cover!</h1>
<p class="abs hero-sub">Create your own phone cover and only pay for the shipping</p>
<div class="abs pill">STRICTLY 1 PER CUSTOMER</div>
<div class="abs btn hero-btn">Create your own design now!</div>
<div class="abs hero-phones" role="img" aria-label="Three phone covers with colourful summer, portrait and cartoon cat designs"></div>
<div class="abs badge hero-badge"><span class="small">VALUED AT</span><span class="price">£7.99</span></div>

<div class="abs limited cond">*** Limited Time Only ***</div>

<!-- info -->
<section class="abs info"></section>
<h2 class="abs info-title cond">Lorem Ipsum Vitae Donec?</h2>
<p class="abs copy info-copy">Quisque vitae velit ac sapien placerat suscipit. Donec mollis justo sed justo pellentesque sollicitudin. Duis bibendum adipiscing nibh. Maecenas diam risus, molestie ut, porta et, malesuada eget, nisi. In fermentum leo sed turpis. Sed lacus velit, consequat in, ultricies sit amet, malesuada et, diam. Integer mauris sem, convallis</p>
<div class="abs info-phone" role="img" aria-label="White phone cover with a repeating red pattern"></div>

<!-- faq -->
<div class="abs rule" style="left:149px;top:1474px;width:362px"></div>
<div class="abs rule" style="left:673px;top:1474px;width:377px"></div>
<div class="abs faq-icon">
  <svg width="128" height="128" viewBox="0 0 128 128">
    <path d="M40 44h48a6 6 0 0 1 6 6v26a6 6 0 0 1-6 6H62l-12 10v-10H40a6 6 0 0 1-6-6V50a6 6 0 0 1 6-6z" fill="#fff"/>
    <text x="64" y="73" text-anchor="middle" font-family="Roboto Condensed,sans-serif" font-weight="700" font-size="28" fill="#3f0c1f">?</text>
  </svg>
</div>
<h2 class="abs faq-title cond">Frequently Asked Questions</h2>
<div class="abs faq-col" style="left:151px;top:1712px">
  <div class="faq-q">When will I get the phone?</div><div class="faq-a">We are on both sides of the big pond to bring you closer<br>to your customers.</div>
  <div class="faq-q">Is it really free?</div><div class="faq-a">We are on both sides of the big pond to bring you closer<br>to your customers.</div>
  <div class="faq-q">What do I pay?</div><div class="faq-a">We are on both sides of the big pond to bring you closer<br>to your customers.</div>
</div>
<div class="abs faq-divider"></div>
<div class="abs faq-col" style="left:650px;top:1712px">
  <div class="faq-q">Shipping Cost</div><div class="faq-a">We are on both sides of the big pond to bring you closer<br>to your customers.</div>
  <div class="faq-q">Where do you ship to?</div><div class="faq-a">We are on both sides of the big pond to bring you closer<br>to your customers.</div>
  <div class="faq-q">What files can I use to upload?</div><div class="faq-a">We are on both sides of the big pond to bring you closer<br>to your customers.</div>
</div>

<!-- offer -->
<section class="abs band"></section>
<h2 class="abs band-title cond">Get your <em>FREE</em> Phone Cover!</h2>
<div class="abs badge band-badge"><span class="small">VALUED AT</span><span class="price">£7.99</span></div>
<div class="abs offer-phones" role="img" aria-label="Three phone covers with colourful summer, portrait and cartoon cat designs"></div>
<p class="abs copy offer-copy">Quisque vitae velit ac sapien placerat suscipit. Donec mollis justo sed justo pellentesque sollicitudin. Duis bibendum adipiscing nibh. Maecenas diam risus, molestie ut, porta et, malesuada eget, nisi. In fermentum leo sed turpis. Sed lacus velit, consequat in, ultricies sit amet, malesuada et, diam. Integer mauris sem, convallis</p>
<div class="abs offer-note">Limited Time Only - 1 Per Customer</div>
<div class="abs cta-box"></div>
<div class="abs btn cta-btn">Create your own design now!</div>

<!-- footer -->
<footer class="abs footer"></footer>
<div class="abs brand footer-brand">
  <div class="brand-mark"></div>
  <div class="brand-name">Brightmoor Gifts</div>
</div>
<div class="abs footer-phone">
  <svg width="20" height="20" viewBox="0 0 24 24"><path d="M6.6 10.8a15.1 15.1 0 0 0 6.6 6.6l2.2-2.2a1 1 0 0 1 1-.25 11.4 11.4 0 0 0 3.6.57 1 1 0 0 1 1 1V20a1 1 0 0 1-1 1A17 17 0 0 1 3 4a1 1 0 0 1 1-1h3.5a1 1 0 0 1 1 1 11.4 11.4 0 0 0 .57 3.6 1 1 0 0 1-.25 1z" fill="#e8150c"/></svg>
  07 000 555 123
</div>
<div class="abs footer-col" style="left:418px"><h4>WHAT WE DO</h4>Information here<br>Information here<br>Information here<br>Information here<br>Information here</div>
<div class="abs footer-col" style="left:605px"><h4>INFORMATION</h4>Information here<br>Privacy Policy<br>Press Kit<br>FAQ</div>
<div class="abs footer-col" style="left:793px"><h4>ABOUT</h4>Contacts<br>Team<br>Support</div>
<div class="abs footer-col" style="left:931px"><h4>FOLLOW</h4>Updates<br>Community<br>Network</div>
<div class="abs bottom-bar"><span style="left:790px">© Brightmoor Gifts, 2018. All Rights Reserved.</span></div>

</body>
</html>
```